50's-style gig poster for a birthday bash

My wife was born in 1957 and is turning 57 next month. I'm throwing a surprise party for her, and thought it would be fun to have a 18x24 poster printed and framed for the event. Attached is a poster from a Rufus Kendrick gig in 1957. I'd like something like this, with a tinted B&W head shot of my wife, with similar fonts and background color schemes. The copy will be LORNA at the top (where the name RUFUS appears), with 57X57 under it, and the word Celebration where the word Quartet currently appears. The rest of the copy will be provided to you. Thanks for your interest and I look forward to working with you.

```html
<!DOCTYPE html>
<html lang="en">
<head>
<meta charset="utf-8">
<title>LORNA 57 x 57 Celebration</title>
<link rel="stylesheet" href="https://fonts.googleapis.com/css2?family=Montserrat:ital,wght@0,600;0,700;0,800;1,500&family=Lobster&family=Alfa+Slab+One&family=Righteous&display=swap">
<style>
  :root {
    --page: #f1f1f0;
    --paper: #ecdfc2;
    --cream: #f5eddc;
    --blue: #1f4a93;
    --navy: #1e3f86;
    --red: #e1202b;
    --ink: #161616;
    --photo-warm: #c98a55;
    --photo-light: #e9c9a0;
  }
  * { margin: 0; padding: 0; box-sizing: border-box; }
  html, body { width: 834px; height: 1200px; overflow: hidden; background: var(--page); }
  .poster {
    position: absolute; left: 34px; top: 29px; width: 766px; height: 1135px;
    background: var(--paper);
    box-shadow: 0 2px 6px rgba(0,0,0,.18);
  }
  .stripe { position: absolute; top: 23px; height: 1091px; width: 127px; }
  .stripe.blue { background: var(--blue); }
  .stripe.red { background: var(--red); }

  .title-row {
    position: absolute; left: 31px; width: 699px;
    display: grid; grid-template-columns: repeat(5, 127px); column-gap: 16px;
    font-family: "Montserrat", sans-serif; font-weight: 700;
    color: var(--cream); text-align: center;
    text-shadow: 5px 5px 0 var(--ink);
  }
  .title-row.name { top: 30px; font-size: 172px; line-height: 150px; }
  .title-row.age { top: 166px; font-size: 166px; line-height: 140px; }
  .title-row .times { font-size: 100px; line-height: 150px; }

  .portrait {
    position: absolute; left: 58px; top: 347px; width: 317px; height: 400px;
    transform: rotate(-3deg);
    border: 4px solid var(--ink);
    background: radial-gradient(ellipse at 55% 45%, var(--photo-light) 0%, var(--photo-warm) 55%, #8a5432 100%);
    box-shadow: 4px 4px 0 rgba(0,0,0,.55);
  }

  .script {
    font-family: "Lobster", cursive; color: var(--cream);
    text-shadow: 4px 4px 0 var(--ink);
  }
  .celebration {
    position: absolute; left: 350px; width: 380px; top: 318px;
    text-align: center; font-size: 72px; transform: rotate(-5deg);
  }
  .lineup {
    position: absolute; left: 360px; width: 390px; top: 420px;
    text-align: center; color: var(--cream);
    font-family: "Montserrat", sans-serif;
    text-shadow: 2px 2px 0 var(--ink);
    list-style: none;
  }
  .lineup .lead { font-style: italic; font-weight: 500; font-size: 21px; line-height: 30px; }
  .lineup li { font-weight: 700; font-size: 21px; line-height: 36.5px; }

  .date-badge {
    position: absolute; left: 407px; top: 720px; width: 241px; height: 118px;
    border-radius: 50%; background: var(--cream); border: 2px solid var(--ink);
    text-align: center; color: var(--navy); padding-top: 14px;
  }
  .date-badge .once { font-family: "Alfa Slab One", serif; font-size: 25px; line-height: 27px; }
  .date-badge .when { font-family: "Montserrat", sans-serif; font-weight: 700; font-size: 15px; line-height: 20px; margin-top: 4px; }

  .also {
    position: absolute; left: 106px; top: 811px; width: 250px; height: 46px;
    background: var(--cream); box-shadow: 4px 4px 0 var(--ink);
    color: var(--navy); font-family: "Montserrat", sans-serif; font-weight: 700;
    font-size: 22px; line-height: 46px; text-align: center;
  }
  .support {
    position: absolute; left: 40px; width: 686px; top: 868px;
    text-align: center; font-size: 66px; line-height: 80px; white-space: nowrap;
  }

  .venue {
    position: absolute; left: 58px; top: 973px; width: 648px; height: 110px;
    background: var(--cream); border: 2px solid var(--ink);
    text-align: center;
  }
  .venue-name {
    font-family: "Righteous", sans-serif; color: var(--ink);
    font-size: 56px; line-height: 62px; letter-spacing: 3px; margin-top: 8px;
  }
  .venue-address {
    font-family: "Montserrat", sans-serif; font-weight: 700; color: var(--navy);
    font-size: 19px; letter-spacing: 2px; line-height: 26px;
  }
</style>
</head>
<body>
  <main class="poster">
    <div class="stripe blue" style="left:31px"></div>
    <div class="stripe red" style="left:175px"></div>
    <div class="stripe blue" style="left:317px"></div>
    <div class="stripe red" style="left:460px"></div>
    <div class="stripe blue" style="left:603px"></div>

    <h1 class="title-row name"><span>L</span><span>O</span><span>R</span><span>N</span><span>A</span></h1>
    <div class="title-row age"><span>5</span><span>7</span><span class="times">x</span><span>5</span><span>7</span></div>

    <div class="portrait" role="img" aria-label="Tinted black and white head shot of Lorna smiling"></div>

    <h2 class="celebration script">Celebration</h2>
    <ul class="lineup">
      <li class="lead">Featuring:</li>
      <li>The Harwoods</li>
      <li>The Wexfords</li>
      <li>The Lawton-Ivers</li>
      <li>The Brantleys</li>
      <li>The Corbetts</li>
      <li>TheCharbonneaus</li>
    </ul>

    <div class="date-badge">
      <div class="once">One Night<br>Only</div>
      <div class="when">April 4, 2014<br>6 PM</div>
    </div>

    <div class="also">Also Appearing</div>
    <div class="support script">The Chirps &amp; Pam Roth</div>

    <div class="venue">
      <div class="venue-name">BISTRO MARCHAND</div>
      <div class="venue-address">1418 Cedar Street, Linden Falls, California</div>
    </div>
  </main>
</body>
</html>
```